Webdesign für Brenner Flusskraft
Zielgruppe
Ansprechpartner für Planung und Errichtung von Stromerzeugung durch erneuerbare Energien. Alle Interessen im privaten, teilöffentlichen und öffentlichen Bereich, die mittel- und langfristig umweltschonenden Strom nutzen wollen.
Aufgabenstellung
- Farben bitte in den Unternehmensfarben Blau/Weiß mit einem kleinen Anteil Orange
- Bilder nach Möglichkeit bitte nur eigene (siehe Anhang)
- klare und übersichtliche Struktur
- KEIN Abklatsch der alten Webseite

```html
<!DOCTYPE html>
<html lang="de">
<head>
<meta charset="utf-8">
<title>Brenner Flusskraft – Kontakt</title>
<link href="https://fonts.googleapis.com/css2?family=Poppins:wght@500;600;800;900&family=Roboto+Condensed:wght@400&display=swap" rel="stylesheet">
<style>
:root{
  --navy:#0b0b8a;
  --sky:#85b0f7;
  --bar:#f1f1f1;
  --text-grey:#6b6b6b;
  --footer:#1b1b1b;
  --white:#fff;
}
*{margin:0;padding:0;box-sizing:border-box}
html,body{width:1200px;height:579px;overflow:hidden;background:var(--white);font-family:"Poppins",sans-serif}
.canvas{position:relative;width:1200px;height:579px;overflow:hidden}
.topbar{position:absolute;left:0;top:0;width:1200px;height:26px;background:var(--bar);border-bottom:1px solid var(--navy);z-index:3}
.topbar .mail-icon{position:absolute;left:223px;top:10px}
.topbar .mail{position:absolute;left:252px;top:7px;font-size:9.5px;font-weight:600;color:var(--navy)}
.topbar .claim{position:absolute;left:0;width:1188px;text-align:center;top:10px;font-size:9.5px;font-weight:500;color:var(--navy)}
.topbar .pin-icon{position:absolute;left:821px;top:7px}
.topbar .addr{position:absolute;left:851px;top:3px;font-size:9.5px;font-weight:500;color:var(--navy);line-height:1.05}
.topbar .addr span{display:block;font-family:"Roboto Condensed",sans-serif;font-size:9px}
.swoosh{position:absolute;left:920px;top:26px}
.career{position:absolute;left:257px;top:26px;width:675px;height:63px;border-radius:0 0 5px 5px;overflow:hidden;display:flex}
.career .photo{width:338px;height:100%;background:linear-gradient(90deg,#2c2e33,#5a5e66 55%,#c9cdd3)}
.career .panel{position:relative;flex:1;background:var(--sky)}
.career .badge{position:absolute;left:-30px;top:-14px;width:60px;height:60px;border-radius:50%;background:var(--white);box-shadow:0 0 0 7px rgba(255,255,255,.25);display:flex;align-items:center;justify-content:center}
.career .kicker{position:absolute;left:62px;top:6px;font-size:7.5px;font-weight:600;letter-spacing:2px;color:var(--white)}
.career .job-mail{position:absolute;left:62px;top:20px;font-size:12px;font-weight:600;color:var(--white)}
.contact-head{position:absolute;right:268px;top:135px;text-align:right}
.contact-head .sub{font-size:8.5px;font-weight:500;color:var(--sky)}
.contact-head h2{font-size:25px;font-weight:900;color:var(--navy);line-height:1;margin-top:9px;letter-spacing:-.3px}
.map{position:absolute;left:257px;top:175px;width:397px;height:375px;background:linear-gradient(160deg,#eef0f3,#e5e8ec 60%,#eceff2)}
.card{position:absolute;left:581px;top:220px;width:351px;height:256px;background:var(--white);box-shadow:0 10px 40px rgba(0,0,0,.08);padding:50px 0 0 50px}
.card h3{font-size:12.5px;font-weight:800;color:var(--navy);line-height:1}
.card p{font-family:"Roboto Condensed",sans-serif;font-size:9px;color:var(--text-grey);margin-top:9px;line-height:1.9}
.card .group{margin-bottom:16px}
.footer{position:absolute;left:0;top:572px;width:1200px;height:7px;background:var(--footer)}
</style>
</head>
<body>
<div class="canvas">
  <header class="topbar">
    <svg class="mail-icon" width="13" height="10" viewBox="0 0 13 10"><rect width="13" height="10" rx="1" fill="#0b0b8a"/><path d="M0.5 1l6 4.5 6-4.5" stroke="#f1f1f1" stroke-width="1.2" fill="none"/></svg>
    <div class="mail">info@brenner-flusskraft.de</div>
    <div class="claim">IHR PROFI FÜR ERNEUERBARE ENERGIEN</div>
    <svg class="pin-icon" width="11" height="15" viewBox="0 0 11 15"><path d="M5.5 0C2.5 0 0 2.4 0 5.4 0 9.4 5.5 15 5.5 15S11 9.4 11 5.4C11 2.4 8.5 0 5.5 0z" fill="#0b0b8a"/><circle cx="5.5" cy="5.3" r="2" fill="#f1f1f1"/></svg>
    <div class="addr">Uferweg 14<span>09120 Talstadt</span></div>
  </header>

  <svg class="swoosh" width="270" height="50" viewBox="0 0 270 50">
    <path d="M12 0H270V1C200 8 90 30 12 45Z" fill="#9a9ad8"/>
    <path d="M12 0H225C160 8 80 24 12 38Z" fill="#3a3aa8"/>
  </svg>

  <section class="career">
    <div class="photo" role="img" aria-label="Foto: Händedruck zweier Geschäftspartner"></div>
    <div class="panel">
      <div class="badge">
        <svg width="32" height="22" viewBox="0 0 32 22"><g transform="rotate(-18 16 11)"><rect x="3" y="3" width="26" height="16" fill="none" stroke="#85b0f7" stroke-width="2"/><path d="M3 3l13 9 13-9" fill="none" stroke="#85b0f7" stroke-width="2"/></g></svg>
      </div>
      <div class="kicker">◢ KARRIERE</div>
      <div class="job-mail">bewerbung@brenner-flusskraft.de</div>
    </div>
  </section>

  <div class="contact-head">
    <div class="sub">JETZT IHREN PROFI FÜR ERNEUERBARE ENERGIEN KONTAKTIEREN</div>
    <h2>KONTAKTBEREICH</h2>
  </div>

  <div class="map" role="img" aria-label="Karte mit dem Standort von Brenner Flusskraft"></div>

  <section class="card">
    <div class="group"><h3>E-Mail</h3><p>info@brenner-flusskraft.de</p></div>
    <div class="group"><h3>Telefon</h3><p>0371 4455620</p></div>
    <div class="group"><h3>Adresse</h3><p>Uferweg 14<br>09120 Talstadt</p></div>
  </section>

  <div class="footer"></div>
</div>
</body>
</html>
```